Verodex business card

Business card for sustainable investment company called "Verodex". Verodex is an exchange platform selling carbon credits between buyers and sellers. Carbon Credits are an environmental commodity for reducing global carbon emissions.

the card should obviously have our logo and the theme should be sustainability/environment mixed with a trading platform.

Contact Information for Business Card

Logo, Name, Title, Phone, Email

Colors
0054AA
0677BA
7BADD7
CADEEF
E8F1F8
0094D4
00A9DD
6FCCEA
C7EBF8
E9F6FB
00AB8E
00BBA5
67D7C9
C6EFE9
E9F9F6
59FF00
82FF00
B8FF75
E3FFCB
F4FFEA

```html
<!DOCTYPE html>
<html lang="en">
<head>
<meta charset="UTF-8">
<title>Verodex Business Card</title>
<link rel="stylesheet" href="https://fonts.googleapis.com/css2?family=Poppins:wght@400;500;600;700&display=swap">
<style>
  :root {
    --stage: #3b3b3d;
    --navy: #0b2a55;
    --navy-deep: #09244b;
    --ink: #0f2340;
    --paper: #f3f4f6;
    --blue: #0094d4;
    --blue-strong: #2a86e0;
    --cyan: #2fd0e6;
    --mark: #2ab8ea;
    --white: #ffffff;
  }
  * { box-sizing: border-box; margin: 0; padding: 0; }
  html, body { width: 1200px; height: 689px; overflow: hidden; }
  body {
    background: var(--stage);
    font-family: "Poppins", sans-serif;
    position: relative;
  }
  .card {
    position: absolute;
    top: 196px;
    width: 520px;
    height: 297px;
    border-radius: 2px;
    overflow: hidden;
  }
  .card--back {
    left: 50px;
    background: linear-gradient(135deg, var(--navy) 0%, var(--navy-deep) 100%);
    display: flex;
    align-items: center;
    justify-content: center;
  }
  .back-brand {
    display: flex;
    align-items: center;
    gap: 14px;
  }
  .back-brand__square {
    width: 30px;
    height: 30px;
    background: var(--mark);
  }
  .back-brand__name {
    font-weight: 700;
    font-size: 46px;
    letter-spacing: 3px;
    color: var(--mark);
  }
  .card--front {
    left: 630px;
    background: var(--paper);
  }
  .front-panel {
    position: absolute;
    inset: 0;
    width: 520px;
    height: 297px;
  }
  .front-brand {
    position: absolute;
    left: 34px;
    top: 170px;
    display: flex;
    align-items: center;
    gap: 10px;
  }
  .front-brand__square {
    width: 18px;
    height: 18px;
    background: var(--blue);
  }
  .front-brand__name {
    font-weight: 600;
    font-size: 26px;
    letter-spacing: 1px;
    color: var(--ink);
  }
  .contact {
    position: absolute;
    right: 26px;
    top: 26px;
    text-align: right;
    color: var(--white);
  }
  .contact__name {
    font-weight: 700;
    font-size: 19px;
    letter-spacing: 0.5px;
    line-height: 1.1;
  }
  .contact__title {
    font-size: 11px;
    font-weight: 400;
    margin-top: 2px;
  }
  .contact__address {
    font-size: 11.5px;
    line-height: 1.45;
    margin-top: 34px;
    margin-right: 22px;
  }
  .contact__list {
    list-style: none;
    margin-top: 12px;
    font-size: 11.5px;
    line-height: 1.55;
  }
  .contact__list li {
    display: flex;
    justify-content: flex-end;
    align-items: center;
    gap: 9px;
  }
  .contact__icon { width: 12px; height: 12px; flex: none; }
</style>
</head>
<body>
  <section class="card card--back" aria-label="Card back">
    <div class="back-brand">
      <span class="back-brand__square"></span>
      <span class="back-brand__name">VERODEX</span>
    </div>
  </section>

  <section class="card card--front" aria-label="Card front">
    <svg class="front-panel" viewBox="0 0 520 297" aria-hidden="true">
      <defs>
        <linearGradient id="panelFill" x1="0" y1="1" x2="1" y2="0">
          <stop offset="0" stop-color="#2a86e0"/>
          <stop offset="1" stop-color="#2fd0e6"/>
        </linearGradient>
      </defs>
      <path d="M268 0 H520 V297 H352 L252 212 Q238 200 236 182 L252 22 Q255 0 268 0 Z" fill="url(#panelFill)"/>
    </svg>

    <div class="front-brand">
      <span class="front-brand__square"></span>
      <span class="front-brand__name">VERODEX</span>
    </div>

    <div class="contact">
      <h1 class="contact__name">DANIEL MARSH</h1>
      <p class="contact__title">Managing Director</p>
      <p class="contact__address">4210 Alder Street<br>Juneau, Alaska 99801</p>
      <ul class="contact__list">
        <li>555-014-2093
          <svg class="contact__icon" viewBox="0 0 12 12"><path d="M3 1 L5 3.5 L4 5 Q5 7 7 8 L8.5 7 L11 9 L9.5 11 Q4 10 1 3 Z" fill="#fff"/></svg>
        </li>
        <li>555-017-6648
          <svg class="contact__icon" viewBox="0 0 12 12"><rect x="3" y="1" width="6" height="10" rx="1" fill="none" stroke="#fff" stroke-width="1.4"/></svg>
        </li>
        <li>info@verodex.com
          <svg class="contact__icon" viewBox="0 0 12 12"><rect x="1" y="2.5" width="10" height="7" fill="#fff"/><path d="M1 2.5 L6 6.5 L11 2.5" fill="none" stroke="#2a9be2" stroke-width="1"/></svg>
        </li>
        <li>www.verodex.com
          <svg class="contact__icon" viewBox="0 0 12 12"><circle cx="6" cy="6" r="5" fill="none" stroke="#fff" stroke-width="1.3"/><path d="M1 6 H11 M6 1 Q3 6 6 11 Q9 6 6 1" fill="none" stroke="#fff" stroke-width="1"/></svg>
        </li>
      </ul>
    </div>
  </section>
</body>
</html>
```